Google Form Graphic to suit our Brand and industry

Create a graphic / image for us to put at the top of our client enquiry google form.
The image will be a section of an architectural home with our branding over the top. Preferably translucent.
The image must suit the shape of the google forms image, which is an elongated rectangle
#003d5d - brand colour

Target Market(s)

residential home owners, high end architectural homes

Industry/Entity Type

Residential construction

Colors
0054AA
0677BA
7BADD7
CADEEF
E8F1F8

Requirements
Must have
• our branding and a photo of an architectural home in the background

```html
<!DOCTYPE html>
<html lang="en">
<head>
<meta charset="utf-8">
<title>New Client Enquiry Form</title>
<link rel="stylesheet" href="https://fonts.googleapis.com/css2?family=Montserrat:wght@600&family=Roboto:wght@400;500&display=swap">
<style>
  :root {
    --page-grey: #e4e4e4;
    --form-cream: #f6efdf;
    --card-white: #ffffff;
    --card-border: #dadce0;
    --section-gold: #deab4f;
    --accent-blue: #4a7df0;
    --required-red: #d93025;
    --text-dark: #202124;
    --text-mid: #3c4043;
    --text-light: #70757a;
    --brand-slate: #3f6379;
    --brand-deep: #2d4f65;
    --brand-light: #5f8399;
  }
  * { box-sizing: border-box; margin: 0; padding: 0; }
  html, body { width: 965px; height: 1200px; overflow: hidden; }
  body {
    background: var(--page-grey);
    font-family: "Roboto", Arial, sans-serif;
    color: var(--text-dark);
    position: relative;
  }
  .form-column {
    position: absolute; left: 100px; top: 0; width: 774px; height: 1200px;
    background: var(--form-cream);
  }
  .header-banner {
    position: absolute; left: 131px; top: 20px; width: 722px; height: 221px;
    background: linear-gradient(100deg, var(--brand-deep) 0%, var(--brand-slate) 35%, var(--brand-light) 60%, var(--brand-slate) 85%, var(--brand-deep) 100%);
    display: flex; align-items: center; justify-content: center;
  }
  .brand-name {
    font-family: "Montserrat", Arial, sans-serif; font-weight: 600;
    color: #ffffff; font-size: 40px; letter-spacing: 9px;
  }
  .section-tab {
    position: absolute; left: 131px; height: 42px;
    background: var(--section-gold); border-radius: 8px 8px 0 0;
    font-size: 18px; color: var(--text-dark);
    padding: 11px 11px 0 11px;
  }
  .section-tab.first { top: 256px; width: 141px; }
  .section-tab.second { top: 1168px; width: 114px; font-size: 13px; padding-top: 10px; height: 40px; }
  .section-rule {
    position: absolute; left: 131px; top: 298px; width: 722px; height: 10px;
    background: var(--section-gold);
  }
  .card {
    position: absolute; left: 131px; width: 722px;
    background: var(--card-white);
    border: 1px solid var(--card-border); border-radius: 8px;
  }
  .title-card { top: 306px; height: 203px; border-top: none; border-radius: 0 0 8px 8px; }
  .form-title {
    position: absolute; left: 24px; top: 64px; width: 595px;
    font-size: 30px; font-weight: 400; color: var(--text-dark);
    padding-bottom: 6px; border-bottom: 1px solid var(--text-dark);
  }
  .toolbar {
    position: absolute; left: 30px; top: 124px; display: flex; gap: 18px;
  }
  .toolbar svg { width: 18px; height: 18px; }
  .form-description {
    position: absolute; left: 24px; top: 163px; font-size: 13.5px; color: var(--text-dark);
  }
  .card-tools { position: absolute; top: 68px; left: 630px; display: flex; gap: 32px; }
  .card-tools svg { width: 16px; height: 20px; }
  .question { height: 128px; }
  .question.active { border-left: 6px solid var(--accent-blue); }
  .question-label {
    position: absolute; left: 23px; top: 31px; font-size: 15px; color: var(--text-dark);
  }
  .question.active .question-label { left: 25px; }
  .required { color: var(--required-red); margin-left: 6px; }
  .answer-line {
    position: absolute; left: 23px; top: 68px; width: 338px;
    font-size: 12.5px; color: var(--text-light);
    padding-bottom: 8px; border-bottom: 1px dotted #9aa0a6;
  }
  .question.active .answer-line { left: 18px; }
  .q-source { top: 523px; }
  .q-name { top: 665px; }
  .q-phone { top: 807px; }
  .q-email { top: 948px; }
  .after-section {
    position: absolute; left: 131px; top: 1096px; display: flex; align-items: center;
    font-size: 13px; color: var(--text-mid);
  }
  .after-section .choice { margin-left: 16px; width: 304px; }
  .after-section svg { width: 10px; height: 6px; }
</style>
</head>
<body>
  <div class="form-column"></div>

  <div class="header-banner" role="img" aria-label="Photo of a bright open-plan architectural home interior with kitchen and balcony, under a translucent slate-blue overlay">
    <span class="brand-name">MARLO BUILD</span>
  </div>

  <div class="section-tab first">Section 1 of 4</div>
  <div class="section-rule"></div>

  <div class="card title-card">
    <h1 class="form-title">New Client Enquiry Form</h1>
    <div class="card-tools">
      <svg viewBox="0 0 16 20"><path d="M4 3l4 4 4-4M4 17l4-4 4 4" fill="none" stroke="#5f6368" stroke-width="1.6"/></svg>
      <svg viewBox="0 0 16 20"><circle cx="8" cy="4" r="1.8" fill="#5f6368"/><circle cx="8" cy="10" r="1.8" fill="#5f6368"/><circle cx="8" cy="16" r="1.8" fill="#5f6368"/></svg>
    </div>
    <div class="toolbar">
      <svg viewBox="0 0 18 18"><text x="4" y="14" font-family="Roboto, sans-serif" font-weight="700" font-size="14" fill="#5f6368">B</text></svg>
      <svg viewBox="0 0 18 18"><text x="5" y="14" font-family="Roboto, sans-serif" font-style="italic" font-size="14" fill="#5f6368">I</text></svg>
      <svg viewBox="0 0 18 18"><text x="4" y="13" font-family="Roboto, sans-serif" font-size="13" fill="#5f6368">U</text><line x1="4" y1="16" x2="14" y2="16" stroke="#5f6368" stroke-width="1.4"/></svg>
      <svg viewBox="0 0 18 18"><rect x="1.5" y="6" width="8" height="6" rx="3" fill="none" stroke="#5f6368" stroke-width="1.6"/><rect x="8.5" y="6" width="8" height="6" rx="3" fill="none" stroke="#5f6368" stroke-width="1.6"/></svg>
      <svg viewBox="0 0 18 18"><path d="M3 4h12M9 4l-3 11M3 3l12 12" fill="none" stroke="#5f6368" stroke-width="1.6"/></svg>
    </div>
    <p class="form-description">We would love to hear your thoughts or feedback on how we can improve your experience!</p>
  </div>

  <div class="card question active q-source">
    <div class="question-label">Firstly, how did you hear about us?<span class="required">*</span></div>
    <div class="answer-line">Short answer text</div>
  </div>

  <div class="card question q-name">
    <div class="question-label">Name</div>
    <div class="answer-line">Short answer text</div>
  </div>

  <div class="card question q-phone">
    <div class="question-label">Phone</div>
    <div class="answer-line">Short answer text</div>
  </div>

  <div class="card question q-email">
    <div class="question-label">Email</div>
    <div class="answer-line">Short answer text</div>
  </div>

  <div class="after-section">
    <span>After section 1</span>
    <span class="choice">Continue to next section</span>
    <svg viewBox="0 0 10 6"><path d="M0 0h10L5 6z" fill="#5f6368"/></svg>
  </div>

  <div class="section-tab second">Section 2 of 4</div>
</body>
</html>
```